PowerPoint Design for KESTREL Polls

KESTREL Polls stands for 'Kindred Evaluation Scales Tracking Regional Electoral Leanings'. It is a collaborative research effort to format and combine multiple sources of public opinion data from around the world into merged datasets. We need a Microsoft PowerPoint design for our conference/workshop presentations and instructional videos used as part of our research efforts and crowdsourced development. The design should match the website design and logo, which are attached to this contest (these are the files from previous successful design contests).

Slides will contain a lot of data visualizations, tables with statistical output (lots of numbers), and figures. Bullet points will be used frequently on slides and larg blocks of text should be avided. Margins should be narrow to maximize space used and the size of fonts must be large enough (24-32+) to be visible at the back of classrooms and conference rooms.
Updates

I was away at a conference and am now busy with teaching preparation, so I need a few extra days to give adequate feedback.

Target Market(s)

academia, government, non-profits, postgraduates, researchers

Font styles to use
Sans Serif

Colors

Designer to choose colors to be used in the design.

Requirements
Must have
• designs for common slide layouts
Nice to have
• thematic link with website design and logo

```html
<!DOCTYPE html>
<html lang="en">
<head>
<meta charset="utf-8">
<title>KESTREL Polls – Title Slide</title>
<link rel="stylesheet" href="https://fonts.googleapis.com/css2?family=Open+Sans:wght@400;600;700&display=swap">
<style>
  :root {
    --brand-blue: #1277bd;
    --brand-blue-faint: #0f6cad;
    --ink-light: #ffffff;
  }
  * { margin: 0; padding: 0; box-sizing: border-box; }
  html, body {
    width: 1200px;
    height: 900px;
    overflow: hidden;
    background: var(--brand-blue);
  }
  .title-slide {
    position: relative;
    width: 1200px;
    height: 900px;
    overflow: hidden;
    background: var(--brand-blue);
    font-family: "Open Sans", Arial, sans-serif;
    color: var(--ink-light);
  }
  .backdrop-disc {
    position: absolute;
    left: -90px;
    top: 360px;
    width: 180px;
    height: 180px;
    border-radius: 50%;
    background: var(--brand-blue-faint);
  }
  .brand-lockup {
    position: absolute;
    right: 45px;
    top: 428px;
    height: 84px;
    display: flex;
    align-items: center;
    gap: 30px;
  }
  .brand-mark {
    width: 64px;
    height: 64px;
    border-radius: 50%;
    background: var(--ink-light);
    flex: none;
  }
  .brand-name {
    font-size: 68px;
    font-weight: 600;
    letter-spacing: 2px;
    line-height: 1;
    white-space: nowrap;
  }
  .project-title {
    position: absolute;
    right: 38px;
    top: 580px;
    font-size: 54px;
    font-weight: 700;
    letter-spacing: 1px;
    line-height: 1.3;
    text-align: right;
    white-space: nowrap;
  }
  .project-subtitle {
    position: absolute;
    right: 38px;
    top: 661px;
    font-size: 31px;
    font-weight: 400;
    line-height: 1.3;
    text-align: right;
    white-space: nowrap;
  }
</style>
</head>
<body>
  <main class="title-slide">
    <span class="backdrop-disc" aria-hidden="true"></span>
    <div class="brand-lockup">
      <span class="brand-mark" aria-hidden="true"></span>
      <span class="brand-name">KESTREL Polls</span>
    </div>
    <h1 class="project-title">PROJECT TITLE HERE</h1>
    <p class="project-subtitle">Subtext here Subtext here</p>
  </main>
</body>
</html>
```